QRV Advisors needs a web site

We need a web site for www.qrvadvisors-example.com. QRV is a mergers and acquisition consulting company that focuses our buyer and seller services on logistics companies. We help put companies together, and help with legal and financial due diligence. We want the web site to express our service and show the logistics components. We want personalized images versus pictures of trucks and airplanes.

Our new logo uses Burgandy and grey colors. Image attached. We are not in to bold, big letters...classy, artistic, low key preferred. Confidentiality, experience, professional are what we want to express on the site.

All we expect for the first part of this project is a home page, and one subpage.  We are budgeting other funds for the technical aspects of the web site

Reason: All that I'm seeing so far is trucks, forklifts and planes. We are a legal mergers and acquisitions firm that focus on logistics. I like some of the images to say logistics, but really want it say legal, financial, and putting companies together. Will pay extra for the sub page if someone can impress us with a home page.

Reason: Swamped with another project at the moment...will work on this over the weekend and provide designer feedback and select final design by Tuesday

```html
<!DOCTYPE html>
<html lang="en">
<head>
<meta charset="utf-8">
<title>QRV Advisors</title>
<link href="https://fonts.googleapis.com/css2?family=Ubuntu:wght@400;500;700&family=Lato:wght@400;700&family=Roboto+Condensed:wght@700&display=swap" rel="stylesheet">
<style>
:root{
  --burgundy:#a50a33;
  --burgundy-dark:#8c0a2b;
  --search-red:#dc0a45;
  --grey:#555a5c;
  --ink:#3a3a3a;
  --panel:#f6f5f5;
  --line:#dcdcdc;
  --footer:#333333;
  --footer-top:#5a5a5a;
  --white:#ffffff;
}
*{box-sizing:border-box;margin:0;padding:0}
html,body{width:1174px;height:1200px;overflow:hidden;background:var(--white)}
body{position:relative;font-family:"Lato",sans-serif;color:var(--ink)}
.abs{position:absolute}

/* header */
.site-header{left:0;top:0;width:1174px;height:103px;background:linear-gradient(#fafafa,#ececec)}
.brand{left:121px;top:30px;font-family:"Ubuntu",sans-serif;font-weight:500;font-size:40px;color:var(--burgundy);letter-spacing:1px}
.phone{left:878px;top:36px;display:flex;align-items:center;gap:12px;font-family:"Ubuntu",sans-serif;font-size:23px;color:var(--burgundy)}

/* nav */
.main-nav{left:0;top:103px;width:1174px;height:49px;background:var(--burgundy)}
.nav-list{left:123px;top:0;display:flex;list-style:none;height:49px}
.nav-list li{font-family:"Ubuntu",sans-serif;font-weight:500;font-size:17.5px;color:var(--white);padding:0 11px;line-height:49px;border-right:1px solid var(--burgundy-dark)}
.nav-list li.active{background:var(--white);color:var(--burgundy);padding:0 22px;border:none;line-height:51px}
.search{left:828px;top:9px;width:213px;height:28px;background:var(--search-red);color:var(--white);font-size:13.5px;font-family:"Ubuntu",sans-serif;padding:6px 10px}
.search svg{position:absolute;right:7px;top:6px}

/* hero */
.hero{left:0;top:152px;width:1174px;height:337px;background:radial-gradient(circle at 790px 140px,#ffffff 0,#fdfdff 40px,#bcd9f5 130px,#5c9fdf 300px,#2f77c7 520px)}
.hero-caption{left:0;top:290px;width:1174px;height:47px;background:rgba(25,30,40,.78);color:var(--white);font-size:21.5px;padding:8px 0 0 131px;font-family:"Lato",sans-serif}
.dots{left:957px;top:306px;display:flex;gap:11px}
.dots span{width:10px;height:10px;border-radius:50%;background:#e6e6e6}
.dots span.on{background:var(--burgundy)}

/* services */
.services{left:305px;top:482px;width:565px;height:84px;border-radius:7px;background:linear-gradient(#ffffff,#e3e3e3);box-shadow:0 2px 4px rgba(0,0,0,.35);display:flex;align-items:center}
.service{display:flex;align-items:center;gap:10px;padding:0 12px;height:58px;border-right:1px solid #cfcfcf}
.service:last-child{border:none}
.service p{font-family:"Ubuntu",sans-serif;font-weight:500;font-size:16.5px;line-height:20px;color:var(--burgundy)}

/* columns */
.card{top:615px;width:296px;height:298px;background:var(--panel);border:1px solid var(--line)}
.card-tab{left:55px;top:-6px;width:187px;height:30px;background:var(--burgundy);color:var(--white);text-align:center;font-family:"Roboto Condensed",sans-serif;font-weight:700;font-size:17px;line-height:30px;border-radius:0 0 3px 3px}
.btn-dark{background:#3a3a3a;color:var(--white);font-family:"Ubuntu",sans-serif;font-size:12.5px;padding:2px 9px;border-radius:4px 4px 0 0}
.mission-photo{left:11px;top:47px;width:276px;height:94px;border:4px solid var(--white);outline:1px solid var(--line);background:linear-gradient(90deg,#6b6258,#d9c6b0 35%,#e7d6c2 55%,#7a6b62 80%,#cfc1b4)}
.mission-text{left:16px;top:154px;width:268px;font-size:12.5px;line-height:18.3px;color:#444}
.news-item{left:14px;width:270px;display:flex;gap:14px;border-bottom:1px solid var(--line);padding-bottom:9px}
.news-item:last-of-type{border:none}
.date{width:34px;flex:none;text-align:center;font-family:"Ubuntu",sans-serif}
.date .m{background:#3a3a3a;color:var(--white);font-size:12px;line-height:16px;border-radius:3px 3px 0 0}
.date .d{background:#cfcfcf;color:#333;font-size:16px;line-height:22px}
.news-item h4{font-family:"Ubuntu",sans-serif;font-weight:400;font-size:13.5px;color:#333;margin-bottom:1px}
.news-item p{font-size:12px;line-height:16px;color:#444}
.form-row{left:19px;display:flex;align-items:flex-start;width:270px;font-size:13.5px;color:#444}
.form-row label{width:66px;padding-top:3px}
.form-row span{display:block;width:186px;height:22px;background:var(--white);border:1px solid #cfcfcf}
.form-row span.area{height:68px}

/* partners */
.partners{left:0;top:946px;width:1174px;height:65px}
.partner{top:18px;display:flex;align-items:center;gap:8px;font-family:"Ubuntu",sans-serif;font-weight:500;font-size:24px;color:#4d6f93}
.partner i{width:14px;height:14px;border-radius:50%;background:#4d6f93}

/* footer */
.site-footer{left:0;top:1033px;width:1174px;height:167px;background:var(--footer);border-top:6px solid var(--footer-top);color:var(--white)}
.site-footer h3{font-family:"Ubuntu",sans-serif;font-weight:400;font-size:17.5px}
.quick-links{list-style:none;font-family:"Ubuntu",sans-serif;font-size:13.5px;line-height:19.5px;margin-top:12px}
.newsletter p{font-size:12.5px;line-height:15.5px;margin-top:12px}
.email-box{margin-top:10px;width:200px;height:23px;background:var(--white);border-radius:3px;color:#888;font-size:12.5px;padding:3px 9px}
.subscribe{margin-top:14px;display:inline-block;background:#8e8e8e;border-radius:3px;font-family:"Ubuntu",sans-serif;font-size:14px;padding:2px 7px}
.social{display:flex;align-items:center;gap:11px;font-family:"Ubuntu",sans-serif;font-size:13.5px;height:26px;margin-top:11px}
.social i{width:26px;height:26px;border-radius:4px;background:#3f74b0}
.footer-brand{left:814px;top:30px;width:220px;text-align:center}
.footer-brand strong{font-family:"Ubuntu",sans-serif;font-weight:500;font-size:44px;color:var(--white);display:block;letter-spacing:2px}
.footer-brand p{font-size:12.5px;line-height:18px;margin-top:18px}
</style>
</head>
<body>

<header class="site-header abs">
  <div class="brand abs">QRV Advisors</div>
  <div class="phone abs">
    <svg width="26" height="26" viewBox="0 0 26 26"><circle cx="13" cy="13" r="11.5" fill="none" stroke="#777" stroke-width="1.6"/><path d="M9 7c1 0 2 2 2 3s-1 1-1 2 2 4 4 4 1-1 2-1 3 1 3 2-1 2-2 2c-4 0-9-5-9-9 0-2 0-3 1-3z" fill="#777"/></svg>
    123 456 7890
  </div>
</header>

<nav class="main-nav abs">
  <ul class="nav-list abs">
    <li class="active">Home</li>
    <li>About Us</li>
    <li>Consulting Services</li>
    <li>News &amp; Events</li>
    <li>FAQ's</li>
    <li style="border:none">Contact Us</li>
  </ul>
  <div class="search abs">Search
    <svg width="15" height="15" viewBox="0 0 15 15"><circle cx="6" cy="6" r="4.5" fill="none" stroke="#fff" stroke-width="2"/><path d="M9.5 9.5l4 4" stroke="#fff" stroke-width="2.4"/></svg>
  </div>
</nav>

<section class="hero abs" role="img" aria-label="Silhouette of a businessman standing against a bright blue sky with the sun shining">
  <div class="hero-caption abs">QRV Services Are Offered By Industry Executives With Extensive M&amp;A Experience</div>
  <div class="dots abs"><span class="on"></span><span></span><span></span><span></span><span></span></div>
</section>

<div class="services abs">
  <div class="service">
    <svg width="62" height="66" viewBox="0 0 62 66"><rect x="4" y="8" width="40" height="54" rx="3" fill="none" stroke="#666" stroke-width="3"/><rect x="10" y="2" width="40" height="54" rx="3" fill="#fff" stroke="#666" stroke-width="3"/><path d="M17 14h26M17 22h26M17 30h26M17 38h18" stroke="#666" stroke-width="3"/><path d="M34 44l7 8 16-16" fill="none" stroke="#666" stroke-width="4"/></svg>
    <p>Bussiness<br>&amp; Planning</p>
  </div>
  <div class="service">
    <svg width="54" height="72" viewBox="0 0 54 72"><path d="M27 2l13 24h-8v12c0 8 10 14 14 34H34c-2-12-7-18-7-18s-5 6-7 18H8c4-20 14-26 14-34V26h-8z" fill="#6a6a6a"/></svg>
    <p>Mergers<br>&amp; Acquisition</p>
  </div>
  <div class="service">
    <svg width="68" height="68" viewBox="0 0 68 68"><circle cx="34" cy="34" r="31" fill="none" stroke="#666" stroke-width="5"/><circle cx="34" cy="34" r="24" fill="none" stroke="#666" stroke-width="2"/><path d="M23 22l6-4 18 24-2 8-7-3z" fill="none" stroke="#666" stroke-width="3"/></svg>
    <p>Advisory<br>Services</p>
  </div>
</div>

<section class="card abs" style="left:121px">
  <div class="card-tab abs">Our Mission</div>
  <div class="mission-photo abs" role="img" aria-label="Group portrait of a diverse business team"></div>
  <p class="mission-text abs">Lorem Ipsum is simply dummy text of the printing and typesetting industry. Lorem Ipsum has been the industry's standard dummy text ever since the 1500sstandard dummy text ever since the 1500s dustry. Lorem Idustry. Lorem I dustry. Lorem.,</p>
  <div class="btn-dark abs" style="right:14px;bottom:0">Read More</div>
</section>

<section class="card abs" style="left:440px">
  <div class="card-tab abs">News &amp; Events</div>
  <div class="news-item abs" style="top:42px">
    <div class="date"><div class="m">APR</div><div class="d">02</div></div>
    <div><h4>Lorem ipsum dolor sit amet</h4><p>Lorem ipsum dol adipiscing elit, seder or sit amet, consectetu industry's standard dummy text ever er</p></div>
  </div>
  <div class="news-item abs" style="top:129px">
    <div class="date"><div class="m">APR</div><div class="d">02</div></div>
    <div><h4>Lorem ipsum dolor sit amet</h4><p>Lorem ipsum dol adipiscing elit, seder or sit amet, consectetu industry's standard dummy text ever er</p></div>
  </div>
  <div class="news-item abs" style="top:218px;border:none">
    <div class="date"><div class="m">APR</div><div class="d">02</div></div>
    <div><h4>Lorem ipsum dolor sit amet</h4><p>Lorem ipsum dol adipiscing elit, seder or sit amet, consectetu</p></div>
  </div>
  <div class="btn-dark abs" style="right:19px;bottom:0">Read More</div>
</section>

<section class="card abs" style="left:758px">
  <div class="card-tab abs">Get in touch</div>
  <div class="form-row abs" style="top:43px"><label>Name</label><span></span></div>
  <div class="form-row abs" style="top:88px"><label>Phone</label><span></span></div>
  <div class="form-row abs" style="top:132px"><label>Email</label><span></span></div>
  <div class="form-row abs" style="top:176px"><label>Message</label><span class="area"></span></div>
  <div class="btn-dark abs" style="right:20px;bottom:0;padding:2px 14px">Submit</div>
</section>

<section class="partners abs">
  <svg class="abs" style="left:137px;top:19px" width="20" height="30" viewBox="0 0 20 30"><path d="M16 2L4 15l12 13" fill="none" stroke="#999" stroke-width="4"/></svg>
  <div class="partner abs" style="left:224px"><i></i>Meridane</div>
  <div class="partner abs" style="left:428px">Harborline Fleet</div>
  <div class="partner abs" style="left:627px"><i></i>Swiftmark</div>
  <div class="partner abs" style="left:827px;color:#666">Loopway</div>
  <svg class="abs" style="left:1031px;top:19px" width="20" height="30" viewBox="0 0 20 30"><path d="M4 2l12 13L4 28" fill="none" stroke="#999" stroke-width="4"/></svg>
</section>

<footer class="site-footer abs">
  <div class="abs" style="left:137px;top:12px">
    <h3>Quick Links</h3>
    <ul class="quick-links">
      <li>Home</li><li>About Us</li><li>Consulting Services</li><li>News &amp; Events</li><li>FAQ's</li><li>Contact Us</li>
    </ul>
  </div>
  <div class="newsletter abs" style="left:337px;top:12px;width:260px">
    <h3>Newsletter</h3>
    <p>Lorem Ipsum is simply dummy text of the printing and typesetting industry.</p>
    <div class="email-box">your e-mail address</div>
    <div class="subscribe">Subscribe</div>
  </div>
  <div class="abs" style="left:636px;top:12px">
    <h3>Follow Us</h3>
    <div class="social"><i></i>Circlebook</div>
    <div class="social"><i style="background:#3aa7d8"></i>Chirper</div>
    <div class="social"><i style="background:#2b7bb4"></i>Proflink</div>
  </div>
  <div class="footer-brand abs">
    <strong>QRV Advisors</strong>
    <p>© 2014 qrvadvisors.<br>All Rights Reserved</p>
  </div>
</footer>

</body>
</html>
```